Business Cards for a law firm

Business cards for our law firm. Use our silhoette logo and OAK PARTNERS - check our website (www.oakpartners.example)

Contact Information for Business Card

our silhouette logo, OAK PARTNERS, 800-555-0147, Dorian Pemberton, dorian@oakpartners.example

Requirements
Must have
• our silhouette logo, OAK PARTNERS, 800-555-0147, Dorian Pemberton, dorian@oakpartners.example

```html
<!DOCTYPE html>
<html lang="en">
<head>
<meta charset="utf-8">
<title>Oak Partners – Business Cards</title>
<link rel="stylesheet" href="https://fonts.googleapis.com/css2?family=Montserrat:wght@400;500;600;700&display=swap">
<style>
  :root {
    --backdrop: #8e939f;
    --paper: #f5f4ee;
    --paper-deco: #fbfaf6;
    --navy: #0f2454;
    --navy-deep: #0a1431;
    --navy-mid: #12204a;
    --amber: #f5a517;
    --white: #ffffff;
    --ink: #1a1f2e;
  }
  * { margin: 0; padding: 0; box-sizing: border-box; }
  html, body { width: 1200px; height: 800px; overflow: hidden; }
  body {
    background: var(--backdrop);
    font-family: "Montserrat", sans-serif;
    position: relative;
  }
  .card {
    position: absolute;
    left: 340px;
    width: 520px;
    height: 291px;
    overflow: hidden;
  }
  .card-front { top: 60px; background: var(--paper); }
  .card-back {
    top: 409px;
    height: 295px;
    background: linear-gradient(180deg, var(--navy-mid) 0%, var(--navy-deep) 100%);
    text-align: center;
    color: var(--white);
  }
  .edge-decoration {
    position: absolute;
    left: 0; top: 40px;
    width: 23px; height: 193px;
    background: var(--paper-deco);
  }
  .brand {
    position: absolute;
    left: 57px; top: 44px;
    display: flex; align-items: center; gap: 14px;
  }
  .brand-mark {
    width: 14px; height: 14px;
    background: var(--navy);
  }
  .brand-name {
    font-size: 20px; font-weight: 600;
    color: var(--navy);
    letter-spacing: 0.06em;
    line-height: 1;
  }
  .brand-tagline {
    margin-top: 8px;
    font-size: 10px; font-weight: 500;
    color: var(--navy);
    letter-spacing: 0.32em;
  }
  .contact-list {
    position: absolute;
    left: 56px; top: 146px;
    list-style: none;
  }
  .contact-list li {
    display: flex; align-items: flex-start; gap: 12px;
    font-size: 13px; font-weight: 500;
    color: var(--ink);
    line-height: 17px;
    margin-bottom: 7.5px;
  }
  .contact-list svg { flex: none; margin-top: 4px; }
  .back-mark {
    width: 18px; height: 18px;
    border-radius: 50%;
    background: var(--amber);
    margin: 120px auto 0;
  }
  .back-name {
    margin-top: 28px;
    font-size: 19px; font-weight: 700;
    letter-spacing: 0.01em;
  }
  .back-sub { margin-top: 2px; font-size: 11px; font-weight: 400; }
  .back-url {
    margin-top: 36px;
    font-size: 10.5px; font-weight: 500;
    color: var(--amber);
  }
</style>
</head>
<body>
  <section class="card card-front">
    <div class="edge-decoration" role="img" aria-label="Faint geometric line ornament along the left edge"></div>
    <div class="brand">
      <span class="brand-mark"></span>
      <div>
        <div class="brand-name">OAK PARTNERS</div>
        <div class="brand-tagline">INJURY ATTORNEYS</div>
      </div>
    </div>
    <ul class="contact-list">
      <li><svg width="9" height="10" viewBox="0 0 9 10"><polygon points="4.5,0 9,2.5 9,7.5 4.5,10 0,7.5 0,2.5" fill="var(--navy)"/></svg>(800) 555-0147</li>
      <li><svg width="9" height="10" viewBox="0 0 9 10"><polygon points="4.5,0 9,2.5 9,7.5 4.5,10 0,7.5 0,2.5" fill="var(--navy)"/></svg>Dorian Pemberton</li>
      <li><svg width="9" height="10" viewBox="0 0 9 10"><polygon points="4.5,0 9,2.5 9,7.5 4.5,10 0,7.5 0,2.5" fill="var(--navy)"/></svg>dorian@oakpartners.example</li>
      <li><svg width="9" height="10" viewBox="0 0 9 10"><polygon points="4.5,0 9,2.5 9,7.5 4.5,10 0,7.5 0,2.5" fill="var(--navy)"/></svg><span>1420 Harbor View Ave #310,<br>Westfield, CA 90000</span></li>
    </ul>
  </section>

  <section class="card card-back" role="img" aria-label="Dark navy card back with subtle chevron pattern">
    <div class="back-mark"></div>
    <div class="back-name">THE OAK PARTNERS®</div>
    <div class="back-sub">Law Firm</div>
    <div class="back-url">www.oakpartners.example</div>
  </section>
</body>
</html>
```